Lo Mara Menu Design Project

This project is pretty straight forward. You will be given 3 files which include the following:
1. Our proposed menu
2. Our Company logo
3. A sample menu on what we are looking for design wise

Your job is to create a visually pleasing menu that is simple, clean and fresh. Please refer to our home website for additional information. (www.lomara-eats.com) Must be in eps or equivalent format.

Target Market(s)

20s to 40s

Industry/Entity Type

It Company

Requirements
Must have
• Company log
Must be in EPS format

```html
<!DOCTYPE html>
<html lang="en">
<head>
<meta charset="utf-8">
<title>Lo Mara — Dim Sum &amp; Starters Menu</title>
<link href="https://fonts.googleapis.com/css2?family=PT+Sans:wght@400;700&family=Tinos:wght@700&display=swap" rel="stylesheet">
<style>
  :root {
    --backdrop: #7b4526;
    --board-dark: #121010;
    --board-mid: #1d1a19;
    --board-grain: #262221;
    --accent-red: #e8241c;
    --header-ink: #1b0d0c;
    --banner-ink: #2b0806;
    --text-light: #f2efec;
    --watermark: #5a3a2e;
  }
  * { box-sizing: border-box; margin: 0; padding: 0; }
  html, body {
    width: 985px;
    height: 1200px;
    overflow: hidden;
    background: var(--backdrop);
  }
  .menu {
    position: absolute;
    left: 42px;
    top: 30px;
    width: 900px;
    height: 1140px;
    background:
      repeating-linear-gradient(90deg, transparent 0 9px, rgba(255,255,255,0.018) 9px 11px, transparent 11px 23px),
      linear-gradient(180deg, var(--board-mid), var(--board-dark) 55%, var(--board-mid));
    box-shadow: 0 0 0 1px var(--board-grain);
    color: var(--text-light);
    font-family: "PT Sans", Arial, sans-serif;
    overflow: hidden;
  }
  .brand-watermark {
    position: absolute;
    left: 207px;
    top: 250px;
    width: 437px;
    height: 537px;
    font-family: "PT Sans", Arial, sans-serif;
    font-weight: 700;
    color: var(--watermark);
    opacity: 0.45;
    text-align: center;
    line-height: 0.9;
  }
  .brand-watermark .line-one { display: block; font-size: 250px; }
  .brand-watermark .line-two { display: block; font-size: 150px; margin-top: 30px; }
  .section-title {
    position: absolute;
    height: 59px;
    background: var(--accent-red);
    color: var(--header-ink);
    font-family: "PT Sans", Arial, sans-serif;
    font-weight: 400;
    font-size: 44px;
    line-height: 59px;
    text-align: center;
    letter-spacing: 0.5px;
  }
  .section-title.dim-sum { left: 316px; width: 247px; top: 39px; }
  .section-title.starters { left: 304px; width: 276px; top: 643px; }
  .dish {
    position: absolute;
    width: 290px;
    text-align: center;
  }
  .dish.col-left { left: -6px; }
  .dish.col-mid { left: 305px; }
  .dish.col-right { left: 542px; }
  .dish-name, .dish-price, .combo-price {
    font-family: "Tinos", "Times New Roman", serif;
    font-weight: 700;
    font-size: 17px;
    line-height: 22px;
  }
  .dish-desc {
    font-size: 14px;
    line-height: 19px;
    margin-top: 5px;
  }
  .combo-banner {
    position: absolute;
    left: 250px;
    top: 887px;
    width: 380px;
    height: 34px;
    background: var(--accent-red);
    color: var(--banner-ink);
    font-family: "Tinos", "Times New Roman", serif;
    font-weight: 700;
    font-size: 16px;
    line-height: 34px;
    text-align: center;
    white-space: pre;
  }
  .combo-price {
    position: absolute;
    left: 0;
    width: 900px;
    top: 932px;
    text-align: center;
  }
  .combo-desc {
    position: absolute;
    left: 130px;
    width: 640px;
    top: 964px;
    text-align: center;
    font-size: 14px;
    line-height: 19px;
  }
  .brand-mark {
    position: absolute;
    left: 735px;
    top: 1048px;
    width: 120px;
    text-align: center;
    font-family: "PT Sans", Arial, sans-serif;
    font-weight: 700;
    font-size: 30px;
    line-height: 32px;
    color: var(--accent-red);
  }
</style>
</head>
<body>
<main class="menu">
  <div class="brand-watermark" aria-hidden="true">
    <span class="line-one">LO</span>
    <span class="line-two">MARA</span>
  </div>

  <h2 class="section-title dim-sum">DIM SUM</h2>

  <article class="dish col-left" style="top:144px">
    <h3 class="dish-name">Pan-Fried Potstickers</h3>
    <p class="dish-price">$ 6.50</p>
    <p class="dish-desc">Five pan-Fried potstickers with<br>chicken or pork.<br>Served with apricot dipping sauce</p>
  </article>
  <article class="dish col-mid" style="top:193px">
    <h3 class="dish-name">Szechuan Dumplings</h3>
    <p class="dish-price">$ 6.25</p>
    <p class="dish-desc">Five chicken dumplings<br>tossed in a spicy cilantro<br>sauce.</p>
  </article>
  <article class="dish col-right" style="top:144px">
    <h3 class="dish-name">Steamed Dumplings</h3>
    <p class="dish-price">$ 6.50</p>
    <p class="dish-desc">Five steamed dumplings with<br>chicken, or&nbsp; vegetables.<br>Served with apricot dipping sauce.</p>
  </article>

  <article class="dish col-left" style="top:286px">
    <h3 class="dish-name">Spring Rolls</h3>
    <p class="dish-price">$ 4.50</p>
    <p class="dish-desc">Two chicken or vegetable<br>spring rolls. Served with apricot<br>dipping sauce</p>
  </article>
  <article class="dish col-mid" style="top:334px">
    <h3 class="dish-name">Wonton Stars</h3>
    <p class="dish-price">$ 7.25</p>
    <p class="dish-desc">Five crispy wonton skins filled<br>with real crab and seasoned cream cheese.<br>Served with sweet and sour dipping sauce.</p>
  </article>
  <article class="dish col-right" style="top:286px">
    <h3 class="dish-name">Bao</h3>
    <p class="dish-price">$ 5.95</p>
    <p class="dish-desc">Three fluffy steamed chinese<br>buns filled with barbeque<br>pork.</p>
  </article>

  <article class="dish col-left" style="top:437px">
    <h3 class="dish-name">Shrimp Toast</h3>
    <p class="dish-price">$ 5.95</p>
    <p class="dish-desc">Four pieces of fried toast with<br>shrimp, onions, bamboo shoots, and<br>water chestnuts. Served with apricot<br>dipping sauce.</p>
  </article>
  <article class="dish col-mid" style="top:484px">
    <h3 class="dish-name">Shu Mai</h3>
    <p class="dish-price">$ 5.95</p>
    <p class="dish-desc">Six steamed open-Face dumplings<br>with pork<br>shrimp, and mushrooms.</p>
  </article>
  <article class="dish col-right" style="top:437px">
    <h3 class="dish-name">Gift Wrapped Chicken</h3>
    <p class="dish-price">$5.95</p>
    <p class="dish-desc">Six chicken breast tenders marinated<br>in soy sauce<br>sesame oil, and cilantro.</p>
  </article>

  <h2 class="section-title starters">STARTERS</h2>

  <article class="dish col-left" style="top:746px">
    <h3 class="dish-name">Lightly Battered Calamari Strips</h3>
    <p class="dish-price">$ 5.95</p>
    <p class="dish-desc">Six calamari strips, lightly battered<br>with a garlic ginger aioli.</p>
  </article>
  <article class="dish col-mid" style="top:774px">
    <h3 class="dish-name">Edamame</h3>
    <p class="dish-price">$ 4.00</p>
    <p class="dish-desc">Steamed Soybean Pods.</p>
  </article>
  <article class="dish col-right" style="top:746px">
    <h3 class="dish-name">House Crab Cakes</h3>
    <p class="dish-price">$11.95</p>
    <p class="dish-desc">Jumbo lump Maryland crab meat<br>with seasoned<br>with our Lo Mara spice blend.<br>Topped with a kick&nbsp; of spicy aioli.</p>
  </article>

  <div class="combo-banner">Pick Your Plates Combo   (Lunch / Dinner)</div>
  <p class="combo-price">$ 14.95 / 18.95</p>
  <p class="combo-desc">Choose three / four half orders: Potstickers, steamed dumplings, szechwan dumplings,<br>spring roll, shrimp toast, chinese chicken salad, hot &amp; sour soup, wonton soup, or mushu,<br>For Shrimp fried rice, beef fried rice, or mushu shrimp, add $1.00.</p>

  <div class="brand-mark">LO<br>MARA</div>
</main>
</body>
</html>
```